Web landing page design

- Create a Web Design (Uncoded - PSD layout only)

We need a single web page design to promote our service. This page will
acts as a landing page for users and also be utilized in social media
advertising. Please provide us with a cutting edge design. I have attached
a link for what the company is about. In essence we are a photo checking
service which reviews photos for retailers, hotels abd car dealerships to
check everything is good after a service has been performed. Whether it be
a new promotion, cleaning or just checking prices. I am looking for a
design to say that we do many photos and at a very cost effective price
(team based in Mexico)

Link: https://slidevault.example/view/qTr8nWx2LpZk4mHcYdJs/
*Deadline*
5 days
*Updates*

- The Start Here box needs to look like this:

-Start Here (heading)
-A box for email addresses to be entered
-Then a check box with "Yes, I have read and agree to the Privacy Policy
and agree to receive email marketing from Plumora88'
-A submit button

All of this information needs to be in one box please. And please feel
free to contact me if you have any questions about this.

*Target Market(s)*
Retail business, Merchandising companies, Rental property owners, Car
dealers
Updates

Please can you submit entries. I am just looking for a tidy to a presentation already created. Just needs design touches.

Target Market(s)

Ability for audience to understand concept quickly
Benefits to why to use the product stand out
Technology driven approach

Industry/Entity Type

Retail

Number of Pages Required

1 page

Colors
0792cd

Requirements
Must have
• Clean and modern design

```html
<!DOCTYPE html>
<html lang="en">
<head>
<meta charset="utf-8">
<title>Checkora – Photo Review Service</title>
<link href="https://fonts.googleapis.com/css2?family=Poppins:wght@400;500;600;700&family=Open+Sans:wght@400&display=swap" rel="stylesheet">
<style>
  :root {
    --brand-blue: #0d7cc4;
    --band-blue: #127dc4;
    --accent-blue: #1a9ad6;
    --ring-blue: #6cb9e2;
    --panel-blue: rgba(9, 125, 200, 0.88);
    --panel-border: #c9ccd0;
    --ink: #1f1f1f;
    --white: #ffffff;
    --footer-text: #333333;
    --social-grey: #6e6e6e;
  }
  * { box-sizing: border-box; margin: 0; padding: 0; }
  html, body { width: 1200px; height: 898px; overflow: hidden; background: var(--white); }
  body { position: relative; font-family: "Poppins", sans-serif; color: var(--white); }

  .hero {
    position: absolute; left: 0; top: 0; width: 1200px; height: 673px;
    background: linear-gradient(100deg, #6f7a86 0%, #5f6e7f 35%, #6b5e5a 58%, #8a8f98 80%, #a2a9b2 100%);
  }
  .hero::after {
    content: ""; position: absolute; inset: 0;
    background: radial-gradient(ellipse at 72% 45%, rgba(170, 90, 70, 0.35), transparent 45%);
  }

  .brand {
    position: absolute; left: 100px; top: 33px; display: flex; align-items: center; gap: 15px;
    font-weight: 600; font-size: 40px; line-height: 48px; color: var(--white);
  }
  .brand-mark { width: 48px; height: 48px; border-radius: 50%; background: var(--accent-blue); }

  .main-nav { position: absolute; top: 44px; left: 646px; display: flex; font-weight: 500; font-size: 17px; letter-spacing: 1px; }
  .main-nav a { color: var(--white); text-decoration: none; position: absolute; white-space: nowrap; }

  .slide-arrow { position: absolute; top: 343px; width: 32px; height: 32px; }
  .slide-arrow.prev { left: 31px; }
  .slide-arrow.next { left: 1137px; }

  .signup {
    position: absolute; left: 107px; top: 208px; width: 331px; height: 286px;
    background: var(--panel-blue); border: 4px solid var(--panel-border);
    padding: 24px 0 0 21px;
  }
  .signup h1 {
    font-weight: 700; font-size: 41px; line-height: 44px; letter-spacing: 1.5px;
    text-shadow: 0 2px 3px rgba(0,0,0,0.25);
  }
  .signup input[type="email"] {
    display: block; margin-top: 15px; width: 281px; height: 44px;
    border: 1px solid #d7d7d7; background: var(--white); padding: 0 14px;
    font-family: "Open Sans", sans-serif; font-size: 11px; color: var(--ink);
  }
  .signup input::placeholder { color: #333; }
  .consent { display: block; margin-top: 14px; width: 290px; font-size: 13px; line-height: 21px; }
  .consent .box {
    display: inline-block; width: 13px; height: 13px; background: var(--white);
    border-radius: 2px; vertical-align: -1px; margin-right: 6px;
  }
  .signup button {
    margin-top: 11px; width: 115px; height: 36px; border: none; background: var(--ink);
    color: var(--white); font-family: "Poppins", sans-serif; font-weight: 600; font-size: 14px;
    letter-spacing: 0.5px; border-radius: 2px;
  }

  .stats-band { position: absolute; left: 0; top: 673px; width: 1200px; height: 154px; background: var(--band-blue); }
  .stat { position: absolute; width: 260px; text-align: center; }
  .stat-ring {
    position: absolute; top: 619px; width: 130px; height: 130px; margin-left: -65px;
    border-radius: 50%; background: var(--white); border: 7px solid var(--ring-blue);
    display: flex; align-items: center; justify-content: center;
    font-weight: 600; font-size: 40px; color: var(--accent-blue);
  }
  .stat-ring.small { font-size: 31px; }
  .stat-label { position: absolute; top: 759px; width: 300px; margin-left: -150px; text-align: center; font-size: 18px; font-weight: 400; letter-spacing: 0.3px; }

  .site-footer { position: absolute; left: 0; top: 827px; width: 1200px; height: 71px; background: var(--white); color: var(--footer-text); font-family: "Open Sans", sans-serif; }
  .copyright { position: absolute; left: 99px; top: 26px; font-size: 14px; }
  .social { position: absolute; left: 820px; top: 20px; display: flex; align-items: center; gap: 6px; font-size: 11px; }
  .social-dot { display: inline-block; width: 28px; height: 28px; border-radius: 50%; background: var(--social-grey); }
  .social-label { margin-right: 4px; }
</style>
</head>
<body>
  <section class="hero" role="img" aria-label="Photo of a smiling woman using a tablet in a bright office with colleagues working in the background"></section>

  <header>
    <div class="brand"><span class="brand-mark"></span>Checkora</div>
    <nav class="main-nav">
      <a href="#" style="left:0">HOME</a>
      <a href="#" style="left:88px">ABOUT</a>
      <a href="#" style="left:183px">RESULTS</a>
      <a href="#" style="left:287px">HOW</a>
      <a href="#" style="left:360px">FREE TRIAL</a>
    </nav>
  </header>

  <svg class="slide-arrow prev" viewBox="0 0 32 32" aria-label="Previous slide">
    <circle cx="16" cy="16" r="15" fill="none" stroke="#fff" stroke-width="1.5"/>
    <path d="M24 16H8M14 10l-6 6 6 6" fill="none" stroke="#fff" stroke-width="1.5"/>
  </svg>
  <svg class="slide-arrow next" viewBox="0 0 32 32" aria-label="Next slide">
    <circle cx="16" cy="16" r="15" fill="none" stroke="#fff" stroke-width="1.5"/>
    <path d="M8 16h16M18 10l6 6-6 6" fill="none" stroke="#fff" stroke-width="1.5"/>
  </svg>

  <form class="signup">
    <h1>START HERE</h1>
    <input type="email" placeholder="Enter email addresses">
    <label class="consent"><span class="box"></span>Yes, I have read and agree to the Privacy Policy and agree to receive email marketing from Plumora88'</label>
    <button type="button">SUBMIT</button>
  </form>

  <section class="stats-band"></section>
  <div class="stat-ring" style="left:218px">2.2M</div>
  <div class="stat-label" style="left:218px">Photos reviewed last year</div>
  <div class="stat-ring" style="left:489px">5P</div>
  <div class="stat-label" style="left:489px">From per photo reviewed</div>
  <div class="stat-ring small" style="left:759px">97.2%</div>
  <div class="stat-label" style="left:759px">Average compliance</div>
  <div class="stat-ring small" style="left:1010px">3-8%</div>
  <div class="stat-label" style="left:1010px">Sales increase</div>

  <footer class="site-footer">
    <p class="copyright">©2018 Checkora , All Rights Reserved.</p>
    <div class="social">
      <span class="social-label">Connect with our social network :</span>
      <span class="social-dot"></span><span class="social-dot"></span><span class="social-dot"></span>
    </div>
  </footer>
</body>
</html>
```